Veltrane Group Business Card Design

The CEO is looking for a new trendy look for his business card.
You can stay with current branding or come up with something new/creative. It can be 3D, including Medical Office buildings. You can use our logo in a variety of colors. Please include name, title, company name, company website, email address, cell number

Target Market(s)

Real Estate Development and Construction

Industry/Entity Type

Health care real estate

Contact Information for Business Card

Rohesh Kamdar, CEO M-604.781.2249 E-roheshkamdar@veltrane.com Address:4180 Lindqvist Ave, Tampa, FL 33482 www.veltrane.com

Font styles to use
Other font styles liked:
• Be creative

Requirements
Must have
• Creative, trendy look
Nice to have
• Please go to our website to get a feel- www. veltrane.com
Should not have
• small fonts

```html
<!DOCTYPE html>
<html lang="en">
<head>
<meta charset="utf-8">
<title>Veltrane Group Business Card</title>
<link href="https://fonts.googleapis.com/css2?family=Montserrat:wght@400;500;700;800&display=swap" rel="stylesheet">
<style>
  :root {
    --canvas: #d3d8d8;
    --paper: #f2f1ee;
    --brand-red: #a80f17;
    --accent-red: #d42a2e;
    --logo-red: #cf2e39;
    --ink: #3a3a3a;
    --shadow: rgba(40, 45, 45, 0.22);
  }
  * { box-sizing: border-box; margin: 0; padding: 0; }
  html, body {
    width: 1200px;
    height: 881px;
    overflow: hidden;
    background: var(--canvas);
    font-family: "Montserrat", sans-serif;
  }
  .stage {
    position: relative;
    width: 1200px;
    height: 881px;
  }
  .card {
    position: absolute;
    top: 297px;
    width: 500px;
    height: 286px;
    border-radius: 3px;
    box-shadow: 0 14px 30px var(--shadow);
  }
  .card-front {
    left: 70px;
    background: var(--paper);
    border-bottom: 3px solid var(--accent-red);
    color: var(--ink);
  }
  .card-back {
    left: 630px;
    background: var(--brand-red);
    display: flex;
    align-items: center;
    justify-content: center;
  }
  .holder {
    position: absolute;
    top: 58px;
    left: 0;
    width: 100%;
    text-align: center;
  }
  .holder-name {
    font-weight: 800;
    font-size: 24px;
    letter-spacing: 0.5px;
    text-transform: uppercase;
    color: var(--accent-red);
  }
  .holder-title {
    margin-top: 4px;
    font-size: 15px;
    font-weight: 500;
    letter-spacing: 1px;
  }
  .details {
    position: absolute;
    top: 148px;
    left: 0;
    width: 100%;
    display: flex;
    justify-content: center;
    align-items: stretch;
    gap: 18px;
  }
  .address {
    text-align: right;
    font-size: 14px;
    line-height: 1.5;
    padding-top: 2px;
  }
  .divider {
    width: 2px;
    background: var(--accent-red);
  }
  .contacts {
    list-style: none;
    font-size: 14px;
    line-height: 1.55;
  }
  .contacts li {
    display: flex;
    align-items: center;
    gap: 8px;
  }
  .contacts svg {
    width: 12px;
    height: 12px;
    fill: var(--accent-red);
    flex: none;
  }
  .brand-name {
    font-weight: 800;
    font-size: 56px;
    letter-spacing: -1px;
    color: var(--logo-red);
    text-align: center;
    line-height: 1;
  }
</style>
</head>
<body>
<main class="stage">
  <section class="card card-front">
    <div class="holder">
      <h1 class="holder-name">Rohesh Kamdar</h1>
      <p class="holder-title">CEO</p>
    </div>
    <div class="details">
      <address class="address" style="font-style:normal">
        4180 Lindqvist Ave<br>Tampa, FL 33482
      </address>
      <span class="divider"></span>
      <ul class="contacts">
        <li>
          <svg viewBox="0 0 12 12" aria-hidden="true"><path d="M3 0h6a1 1 0 0 1 1 1v10a1 1 0 0 1-1 1H3a1 1 0 0 1-1-1V1a1 1 0 0 1 1-1zm0.5 1.5v7.5h5V1.5zM6 9.8a0.7 0.7 0 1 0 0 1.4a0.7 0.7 0 0 0 0-1.4z"/></svg>
          604.781.2249
        </li>
        <li>
          <svg viewBox="0 0 12 12" aria-hidden="true"><path d="M0 2h12v8H0zm1 1v0.4l5 3.3l5-3.3V3zm0 1.6V9h10V4.6L6 7.9z"/></svg>
          roheshkamdar@veltrane.com
        </li>
        <li>
          <svg viewBox="0 0 12 12" aria-hidden="true"><circle cx="6" cy="6" r="6"/></svg>
          www.veltrane.com
        </li>
      </ul>
    </div>
  </section>

  <section class="card card-back">
    <p class="brand-name">Veltrane Group</p>
  </section>
</main>
</body>
</html>
```